Harborlight Amusement Collective (HAC)

We need a business card design for Harborlight Amusement Collective. Modern and sleek looking, with all critical information. Open to single or double sided designs, if double sided info needs to be all on one side. The main Logo is Harborlight Amusement collective and must be on the card. The other three logos are for the brands that fall under the group, they might be good on the back.

Industry/Entity Type

Business

```html
<!DOCTYPE html>
<html lang="en">
<head>
<meta charset="utf-8">
<title>Harborlight Amusement Collective – Business Card</title>
<link rel="stylesheet" href="https://fonts.googleapis.com/css2?family=Montserrat:wght@500;600;700&display=swap">
<style>
  :root{
    --bg:#e4e4e4;
    --ink:#0b0b0b;
    --paper:#ffffff;
    --blue:#2a5ba8;
    --green:#8db83a;
    --text:#2b2b2b;
    --muted:#5a5a5a;
    --faint:#eef0f3;
    --divider:#9a9a9a;
  }
  *{box-sizing:border-box;margin:0;padding:0}
  html,body{width:1200px;height:852px;overflow:hidden}
  body{background:var(--bg);font-family:"Montserrat",Arial,sans-serif;color:var(--text);position:relative}

  .card{position:absolute;top:266px;width:540px;height:320px;border-radius:22px;overflow:hidden;box-shadow:0 8px 22px rgba(0,0,0,.18)}
  .card--front{left:40px;background:var(--ink)}
  .card--back{left:620px;background:var(--paper)}

  /* front */
  .front-brand{position:absolute;top:70px;left:0;right:0;text-align:center}
  .wordmark{display:inline-flex;align-items:center;gap:12px;color:var(--blue);font-weight:700;letter-spacing:.5px}
  .wordmark__mark{width:16px;height:16px;background:var(--green)}
  .wordmark__name{font-size:20px;line-height:1.15;text-align:left;text-transform:uppercase}
  .front-brands{position:absolute;left:0;right:0;bottom:0;height:112px;background:var(--paper)}
  .brand-row{display:flex;align-items:center;justify-content:space-around;height:70px;padding:0 14px}
  .brand{display:flex;align-items:center;gap:7px;color:var(--blue);font-weight:700;font-size:15px}
  .brand__dot{width:12px;height:12px;border-radius:50%;background:var(--green)}
  .brand-sep{width:1px;height:34px;background:var(--divider)}
  .front-url{position:absolute;left:0;right:0;bottom:12px;text-align:center;font-size:12px;color:var(--muted);font-weight:500}
  .front-url::before,.front-url::after{content:"";display:inline-block;width:40px;height:2px;background:var(--green);vertical-align:middle;margin:0 12px}

  /* back */
  .back-decor{position:absolute;right:0;top:0;width:250px;height:230px;background:linear-gradient(135deg,var(--faint),#f8f9fa)}
  .back-brand{position:absolute;left:34px;top:112px}
  .back-brand .wordmark__name{font-size:17px}
  .contact{position:absolute;left:292px;top:36px;color:var(--text)}
  .contact__name{font-size:20px;font-weight:700;color:var(--blue)}
  .contact__role{font-size:12px;font-weight:500;margin-bottom:20px}
  .contact__addr{font-size:12px;line-height:1.4;margin-bottom:12px}
  .contact__list{list-style:none;font-size:12px;line-height:1.75}
  .contact__list li{display:flex;align-items:center;gap:9px}
  .contact__list svg{width:12px;height:12px;fill:var(--blue)}
  .accent-green{position:absolute;left:0;bottom:0;width:300px;height:14px;background:var(--green)}
  .company-tab{position:absolute;right:0;bottom:0;width:250px;height:56px;background:var(--blue);border-top-left-radius:18px;color:#fff;font-size:12px;font-weight:500;display:flex;align-items:center;justify-content:center}
</style>
</head>
<body>

<section class="card card--front" aria-label="Card front">
  <div class="front-brand">
    <div class="wordmark">
      <span class="wordmark__mark"></span>
      <span class="wordmark__name">Harborlight<br>Amusement Collective</span>
    </div>
  </div>
  <div class="front-brands">
    <div class="brand-row">
      <span class="brand"><span class="brand__dot"></span>Tidewater Tickets</span>
      <span class="brand-sep"></span>
      <span class="brand"><span class="brand__dot"></span>Boxseat Hospitality</span>
      <span class="brand-sep"></span>
      <span class="brand"><span class="brand__dot"></span>Gatepoint Passes</span>
    </div>
    <p class="front-url">www.harborlightcollective.com</p>
  </div>
</section>

<section class="card card--back" aria-label="Card back">
  <div class="back-decor" role="img" aria-label="Faint background area for the group emblem"></div>
  <div class="back-brand">
    <div class="wordmark">
      <span class="wordmark__mark"></span>
      <span class="wordmark__name">Harborlight<br>Amusement<br>Collective</span>
    </div>
  </div>
  <div class="contact">
    <h1 class="contact__name">Jordan Ames Reyes</h1>
    <p class="contact__role">Managing Director</p>
    <p class="contact__addr">48 Quayside Ave., Port Town,<br>US 123456</p>
    <ul class="contact__list">
      <li><svg viewBox="0 0 12 12"><path d="M2.5 1h2l1 3-1.3 1a6 6 0 0 0 2.8 2.8L8 6.5l3 1v2a1.5 1.5 0 0 1-1.5 1.5A8.5 8.5 0 0 1 1 2.5 1.5 1.5 0 0 1 2.5 1z"/></svg>555.012.3456</li>
      <li><svg viewBox="0 0 12 12"><path d="M0 2h12v8H0zM1 3l5 3.5L11 3v-.2H1z" fill-rule="evenodd"/></svg>jreyes@harborlightcollective.com</li>
      <li><svg viewBox="0 0 12 12"><circle cx="6" cy="6" r="5.5"/></svg>www.harborlightcollective.com</li>
    </ul>
  </div>
  <div class="accent-green"></div>
  <div class="company-tab">Harborlight Amusement Collective Ltd</div>
</section>

</body>
</html>
```